Valderons Business Card

Business card for philanthropic organization

Industry/Entity Type

Business

Contact Information for Business Card

Need a very ELEGANT, sober, embossed, formal business card... it should transmit CREDIBILITY. Not looking for a "fun card". would like white, grays or black designs.

Font styles to use
Script

Requirements
Must have
• Embossed look

```html
<!DOCTYPE html>
<html lang="en">
<head>
<meta charset="utf-8">
<title>Valderons Business Card</title>
<link rel="stylesheet" href="https://fonts.googleapis.com/css2?family=Italianno&family=Open+Sans:wght@400&display=swap">
<style>
  :root {
    --page: #d9d6d1;
    --card-deep: #050505;
    --card-mid: #1c1c1c;
    --card-sheen: #3a3a3a;
    --ink: #f4f4f4;
    --ink-soft: #cfcfcf;
    --emboss-dark: rgba(0,0,0,0.85);
    --emboss-light: rgba(255,255,255,0.18);
  }
  * { margin: 0; padding: 0; box-sizing: border-box; }
  html, body {
    width: 1200px;
    height: 1023px;
    overflow: hidden;
    background: var(--page);
  }
  .canvas {
    width: 1200px;
    height: 1023px;
    display: flex;
    align-items: center;
    justify-content: center;
  }
  .business-card {
    position: relative;
    width: 1000px;
    height: 572px;
    border-radius: 6px;
    background:
      linear-gradient(100deg, transparent 30%, rgba(255,255,255,0.06) 48%, transparent 62%),
      radial-gradient(ellipse at 45% 55%, var(--card-sheen) 0%, var(--card-mid) 38%, var(--card-deep) 78%);
    box-shadow: 0 24px 50px rgba(0,0,0,0.35);
    color: var(--ink);
    overflow: hidden;
  }
  .brand {
    position: absolute;
    left: 110px;
    top: 340px;
    display: flex;
    align-items: center;
    gap: 14px;
  }
  .brand-dot {
    width: 18px;
    height: 18px;
    border-radius: 50%;
    background: var(--ink-soft);
  }
  .brand-name {
    font-family: "Open Sans", sans-serif;
    font-weight: 400;
    font-size: 34px;
    letter-spacing: 2px;
    color: var(--ink-soft);
  }
  .contact-block {
    position: absolute;
    left: 560px;
    top: 120px;
  }
  .person-name {
    font-family: "Italianno", cursive;
    font-size: 78px;
    line-height: 1;
    color: var(--ink);
    text-shadow: -1px -1px 0 var(--emboss-light), 2px 2px 2px var(--emboss-dark);
  }
  .person-title {
    font-family: "Italianno", cursive;
    font-size: 34px;
    line-height: 1;
    margin: 4px 0 26px 40px;
    color: var(--ink-soft);
    text-shadow: 1px 1px 1px var(--emboss-dark);
  }
  .contact-list {
    list-style: none;
    font-family: "Open Sans", sans-serif;
    font-size: 22px;
    line-height: 40px;
    color: var(--ink);
    text-shadow: 1px 1px 1px var(--emboss-dark);
  }
</style>
</head>
<body>
  <main class="canvas">
    <section class="business-card">
      <div class="brand">
        <span class="brand-dot"></span>
        <span class="brand-name">Valderons</span>
      </div>
      <div class="contact-block">
        <h1 class="person-name">Daniel Sterling</h1>
        <p class="person-title">Director</p>
        <ul class="contact-list">
          <li>C: +(507)-6123-4400</li>
          <li>E: dsterling@valderons.org</li>
          <li>A: P.O. Box 0812-04417</li>
          <li>Panama, Republic of Panama</li>
        </ul>
      </div>
    </section>
  </main>
</body>
</html>
```